kolvarin.link kolvarin.space kolvarin.press website

The website is named KOLVARIN and it will have 3 domain names. kolvarin.link, press, space.
I'd like it to be viewed on Pads, pcs and phones.

page menu:

kolvarin.link(start page): presentation of company. (creative, design, app, new product innovation.)
Here we'll need sosial media icons: plimber, vendoloop, mirtavel, trelvanet. (light but some 'fruity' colors)

kolvarin.press: blog. It will be a 75% picture blog > rest will be text. I need to be able to resize pictures and shape columns to picture size. (light but some 'fruity' colors)

kolvarin.space : the fun part of this web design, however, on entering the page I'd like a non-disclosure agreement where viewer simply click "yes, I agree" after filling out contact info. (check attached document)
We will have space here for uploading PDF files viewers can download. There is also a blog space here to tell in brief about the PDF file. (maybe a space/sci-fi theme her e.g spacechimp, Laika the space dog?)

I will attach the logo here I want you to use > and develop for the .space .press webpage. The logo i uploaded is for the .link page.

Target Market(s)

venture capitalists

Number of Pages Required

3 page

Requirements
Must have
• a few 'fruity colors' but mostly white and grey

```html
<!DOCTYPE html>
<html lang="en">
<head>
<meta charset="utf-8">
<title>KOLVARIN — Creative studio</title>
<link rel="stylesheet" href="https://fonts.googleapis.com/css2?family=Silkscreen&family=Lato:wght@400;700&family=Source+Sans+3:wght@400;600&display=swap">
<style>
:root{
  --ink:#4a5f80;
  --ink-soft:#6a7b95;
  --text:#5d6a7e;
  --accent:#e2462f;
  --orange:#f39a1e;
  --green:#4f9a3a;
  --topbar:#f3f5f8;
  --panel:#eef2f7;
  --white:#ffffff;
  --footer:#262626;
  --footer-base:#1b1b1b;
  --fruit-orange:#f0a12a;
  --fruit-red:#d8432b;
  --fruit-blue:#2f7fc1;
  --fruit-pink:#d93a55;
}
*{box-sizing:border-box;margin:0;padding:0}
html,body{width:1200px;height:2314px;overflow:hidden;background:var(--white)}
body{font-family:"Source Sans 3",Arial,sans-serif;color:var(--text)}
.container{width:732px;margin:0 auto;position:relative}
.display{font-family:"Silkscreen","Courier New",monospace;font-weight:400;letter-spacing:3px;text-transform:uppercase;color:var(--ink)}

/* top bar */
.topbar{height:25px;background:var(--topbar);font-size:8px;color:var(--ink-soft)}
.topbar .container{display:flex;align-items:center;height:25px;gap:14px}
.topbar .contact{display:flex;align-items:center;gap:4px}
.topbar .search{margin-left:auto}

/* header */
.header{height:71px;background:var(--white)}
.header .container{display:flex;align-items:center;height:71px}
.brand{display:flex;align-items:center;gap:6px;font-family:"Lato",sans-serif;font-weight:700;font-size:15px;color:#2e2e2e;letter-spacing:1px}
.brand-mark{width:12px;height:12px;background:var(--fruit-orange)}
.nav{display:flex;gap:26px;margin-left:80px;font-family:"Lato",sans-serif;font-size:10px;text-transform:uppercase;color:#333}
.nav .active{color:var(--accent)}
.social{display:flex;gap:10px;margin-left:24px;font-family:"Lato",sans-serif;font-size:9px;color:#333}
.social li{list-style:none;display:flex;align-items:center;gap:4px}
.social i{display:block;width:9px;height:9px;border-radius:2px}
.c-orange{background:var(--fruit-orange)}.c-red{background:var(--fruit-red)}.c-blue{background:var(--fruit-blue)}.c-pink{background:var(--fruit-pink)}

/* hero */
.hero{height:549px;position:relative;overflow:hidden;text-align:center}
.hero-photo{position:absolute;inset:0;background:radial-gradient(ellipse at 60% 30%,#6f7a6d 0%,#5a4536 35%,#3b2c22 70%,#251b16 100%)}
.hero-shade{position:absolute;inset:0;background:rgba(20,20,30,.35)}
.hero-content{position:relative;padding-top:178px}
.hero h1{font-size:46px;color:var(--white);letter-spacing:6px}
.hero p{width:640px;margin:14px auto 0;font-size:13.5px;line-height:20px;color:#d9dde3}
.btn{display:inline-block;background:var(--accent);color:var(--white);font-family:"Lato",sans-serif;font-weight:700;text-transform:uppercase;box-shadow:0 2px 0 #b8321f}
.hero .btn{margin-top:34px;width:185px;height:40px;line-height:40px;font-size:10px}
.dots{display:flex;justify-content:center;gap:6px}
.dots span{width:6px;height:6px;border-radius:50%;background:var(--white)}
.hero .dots{position:absolute;left:0;right:0;top:626px;top:auto;bottom:17px}
.hero .dots span:first-child{background:var(--orange)}

/* welcome */
.welcome{height:419px;text-align:center;padding-top:76px}
.welcome h2{font-size:30px}
.lead{margin:22px auto 0;width:520px;font-size:13.5px;line-height:21px;color:var(--ink-soft)}
.features{display:flex;text-align:left;margin-top:42px;width:732px;margin-left:auto;margin-right:auto}
.feature{width:250px;display:flex;gap:14px;padding-left:10px}
.feature svg{flex:none;margin-top:2px}
.feature h3{font-family:"Lato",sans-serif;font-weight:700;font-size:16px;color:var(--ink)}
.feature p{margin-top:10px;width:172px;font-size:9.5px;line-height:15.5px;color:var(--ink-soft)}

/* works */
.works{height:794px;background:var(--panel);text-align:center;padding-top:78px}
.works h2{font-size:30px}
.works .sub{margin-top:14px;font-size:13px;color:var(--ink-soft)}
.cards{display:flex;gap:18px;width:732px;margin:46px auto 0}
.card{width:357px;background:var(--white)}
.card .photo{height:243px}
.card h4{margin-top:20px;font-family:"Lato",sans-serif;font-weight:700;font-size:12.5px;color:var(--ink)}
.card span{display:block;margin-top:4px;padding-bottom:20px;font-size:8.5px;color:#8b97a8}
.thumbs{display:flex;gap:20px;width:732px;margin:53px auto 0}
.thumbs div{width:169px;height:115px}
.works .dots{margin-top:28px}
.works .dots span{background:var(--ink);width:8px;height:8px}
.works .dots span:nth-child(2){background:var(--accent)}
.ph-a{background:linear-gradient(135deg,#6b8b55,#ded8cc 55%,#8a6b4c)}
.ph-b{background:linear-gradient(135deg,#b9cfe0,#e6ecf1 50%,#3b5f96)}
.ph-c{background:linear-gradient(135deg,#2d4a5c,#7fa3b6)}
.ph-d{background:linear-gradient(135deg,#3a3a3a,#4d4d4d)}
.ph-e{background:linear-gradient(135deg,#d9822e,#7d5a3d 60%,#c9b08e)}
.ph-f{background:linear-gradient(135deg,#6c4a34,#c9c0b3 60%,#4a3528)}

/* cta */
.cta{height:247px;text-align:center;padding-top:60px}
.cta h2{font-size:28px}
.cta p{margin:18px auto 0;font-size:13px;line-height:22px;color:var(--ink-soft)}
.cta .btn{margin-top:14px;width:92px;height:31px;line-height:31px;font-size:8px}

/* footer */
.footer{height:177px;background:var(--footer);text-align:center;padding-top:58px}
.footer-links{display:flex;justify-content:center;font-size:10px;color:#e4e4e4}
.footer-links a{color:inherit;text-decoration:none;padding:0 12px;border-left:1px solid #e4e4e4;line-height:16px}
.footer-links a:first-child{border-left:none}
.footer .social{justify-content:center;margin:32px 0 0;color:#e4e4e4}
.base{height:32px;background:var(--footer-base);text-align:center;line-height:32px;font-size:8.5px;color:#d0d0d0}
</style>
</head>
<body>

<div class="topbar">
  <div class="container">
    <span class="contact">
      <svg width="9" height="7" viewBox="0 0 9 7"><rect x=".5" y=".5" width="8" height="6" fill="none" stroke="#6a7b95"/><path d="M.5 .5 4.5 4 8.5 .5" fill="none" stroke="#6a7b95"/></svg>
      hello@kolvarin.link
    </span>
    <span class="contact">
      <svg width="6" height="9" viewBox="0 0 6 9"><rect x=".5" y=".5" width="5" height="8" rx="1" fill="none" stroke="#6a7b95"/></svg>
      +00 (555) 014 22 37
    </span>
    <svg class="search" width="8" height="8" viewBox="0 0 8 8"><circle cx="3.2" cy="3.2" r="2.5" fill="none" stroke="#6a7b95"/><path d="M5 5 7.5 7.5" stroke="#6a7b95"/></svg>
  </div>
</div>

<header class="header">
  <div class="container">
    <div class="brand"><span class="brand-mark"></span>KOLVARIN</div>
    <nav class="nav">
      <span class="active">Home</span><span>About us</span><span>Gallery</span><span>Services</span><span>Projects</span><span>Contact us</span>
    </nav>
    <ul class="social">
      <li><i class="c-orange"></i>plimber</li>
      <li><i class="c-red"></i>trelvanet</li>
      <li><i class="c-blue"></i>mirtavel</li>
      <li><i class="c-pink"></i>vendoloop</li>
    </ul>
  </div>
</header>

<section class="hero">
  <div class="hero-photo" role="img" aria-label="Photo of a designer's desk with a laptop, sketches, glasses and a cup of coffee"></div>
  <div class="hero-shade"></div>
  <div class="hero-content">
    <h1 class="display">Contatnry Popilar</h1>
    <p>Lorem ipsum dolor sit amet, consectetur adipiscing elit. Nunc dignissim iaculis sapien, eu volutpat lorem. Proin pharetra arcu a ipsum facilisis</p>
    <span class="btn">Get started now</span>
  </div>
  <div class="dots"><span></span><span></span><span></span><span></span></div>
</section>

<section class="welcome">
  <h2 class="display">Welcome to our site</h2>
  <p class="lead">Sed ultrices dui et consectetur consequat. Pellentesque non elit quis nulla consequat euismod. Proin finibus ligula id elit congue accumsan. Donec vitae enim feugiat, maximus mauris quis, commodo justo.</p>
  <div class="features">
    <div class="feature">
      <svg width="20" height="30" viewBox="0 0 20 30"><rect x="2" y="1" width="16" height="28" rx="2" fill="none" stroke="#e2462f" stroke-width="2"/><rect x="6" y="14" width="2" height="8" fill="#e2462f"/><rect x="9" y="10" width="2" height="12" fill="#e2462f"/><rect x="12" y="17" width="2" height="5" fill="#e2462f"/><circle cx="10" cy="25.5" r="1.2" fill="#e2462f"/></svg>
      <div><h3>App Creation</h3><p>Magnis modipsae que lib voloratati andigen daepeditem quiate re porem aut labor. Laceaque quiae sitiorem rest non restibusaes maio es dem tumquam core posae volor remped modis volor.</p></div>
    </div>
    <div class="feature">
      <svg width="22" height="32" viewBox="0 0 22 32"><path d="M11 2a9 9 0 0 0-5 16.5V23h10v-4.5A9 9 0 0 0 11 2z" fill="none" stroke="#f39a1e" stroke-width="2.2"/><path d="M7 26h8M8 29h6" stroke="#f39a1e" stroke-width="2"/></svg>
      <div><h3>Creative Design</h3><p>Magnis modipsae que lib voloratati andigen daepeditem quiate re porem aut labor. Laceaque quiae sitiorem rest non restibusaes maio es dem tumquam core posae volor remped modis volor.</p></div>
    </div>
    <div class="feature">
      <svg width="32" height="30" viewBox="0 0 32 30"><path d="M16 2l4.1 8.6 9.4 1.2-6.9 6.5 1.8 9.3L16 23.1l-8.4 4.5 1.8-9.3-6.9-6.5 9.4-1.2z" fill="none" stroke="#4f9a3a" stroke-width="2.2" stroke-linejoin="round"/></svg>
      <div><h3>New Product Innovation</h3><p>Magnis modipsae que lib voloratati andigen daepeditem quiate re porem aut labor. Laceaque quiae sitiorem rest non restibusaes maio es dem tumquam core posae volor remped modis volor.</p></div>
    </div>
  </div>
</section>

<section class="works">
  <h2 class="display">Our latest works</h2>
  <p class="sub">Magnis modipsae que voloratati andigen daepeditem quiate re porem aut labor.</p>
  <div class="cards">
    <article class="card">
      <div class="photo ph-a" role="img" aria-label="Photo of hands holding a smartphone over wireframe sketches beside a laptop and coffee"></div>
      <h4>Grand Motel gets an identity brushup</h4><span>Identity</span>
    </article>
    <article class="card">
      <div class="photo ph-b" role="img" aria-label="Photo of a designer working at a laptop with printed layouts on the desk"></div>
      <h4>Fresh branding for a creative startup</h4><span>Identity</span>
    </article>
  </div>
  <div class="thumbs">
    <div class="ph-c" role="img" aria-label="Photo of a hand with a glowing digital interface"></div>
    <div class="ph-d" role="img" aria-label="Chalkboard sketch of a website structure diagram"></div>
    <div class="ph-e" role="img" aria-label="Photo of a laptop on a sunlit wooden desk"></div>
    <div class="ph-f" role="img" aria-label="Photo of a web design workspace with a monitor and coffee"></div>
  </div>
  <div class="dots"><span></span><span></span><span></span></div>
</section>

<section class="cta">
  <h2 class="display">Want to work with us?</h2>
  <p>Magnis modipsae que voloratati andigen daepeditem quiate re porem aut labor.<br>Laceaque quiae sitiorem rest non restibusaes maio es dem tumquam.</p>
  <span class="btn">Get in touch</span>
</section>

<footer class="footer">
  <nav class="footer-links"><a>Home</a><a>Privacy Policy</a><a>Terms &amp; Conditions</a><a>Contacts</a></nav>
  <ul class="social">
    <li><i class="c-orange"></i>plimber</li>
    <li><i class="c-red"></i>trelvanet</li>
    <li><i class="c-blue"></i>mirtavel</li>
    <li><i class="c-pink"></i>vendoloop</li>
  </ul>
</footer>
<div class="base">© 2016 Kolvarin . All rights reserved.</div>

</body>
</html>
```